dsadasdasdasdsa

Industry/Entity Type

Mortgage Broking

Requirements
Must have
• Call-to-action button somewhere on the graphic
Nice to have
• The font of our logo is Montserrat

```html
<!DOCTYPE html>
<html lang="en">
<head>
<meta charset="UTF-8">
<title>Mortgage Broker Directory Banner</title>
<link href="https://fonts.googleapis.com/css2?family=Montserrat:wght@600;700;800;900&display=swap" rel="stylesheet">
<style>
  :root {
    --bg-light: #f6faf0;
    --bg-mint: #dff2c6;
    --panel-green: #1e6b3c;
    --panel-green-deep: #175a31;
    --headline-yellow: #f4ea2a;
    --text-white: #ffffff;
    --cta-red: #c23b2b;
    --cta-red-light: #e2612f;
    --button-yellow: #f2ee2d;
    --button-text: #1a4a24;
    --mascot-green: #5fae4e;
    --mascot-brown: #9a5a2a;
  }
  * { margin: 0; padding: 0; box-sizing: border-box; }
  html, body { width: 1200px; height: 180px; overflow: hidden; }
  body { font-family: "Montserrat", sans-serif; }
  .banner {
    position: relative;
    width: 1200px;
    height: 180px;
    overflow: hidden;
    background: linear-gradient(90deg, var(--bg-light) 0%, var(--bg-mint) 60%, var(--bg-light) 100%);
  }
  .banner__shapes { position: absolute; inset: 0; }
  .message {
    position: absolute;
    left: 29px;
    width: 667px;
    top: 0;
    height: 180px;
    text-align: center;
    color: var(--text-white);
  }
  .message__question {
    position: absolute;
    left: 0; right: 0;
    top: 22px;
    font-size: 31px;
    font-weight: 600;
    color: var(--headline-yellow);
    letter-spacing: 0.2px;
  }
  .message__rule {
    position: absolute;
    left: 105px; right: 105px;
    top: 70px;
    border-top: 2px dotted rgba(255,255,255,0.55);
  }
  .message__line {
    position: absolute;
    left: 0; right: 0;
    font-weight: 900;
    text-transform: uppercase;
    line-height: 1;
  }
  .message__line--search { top: 88px; font-size: 28px; }
  .message__line--directory { top: 124px; font-size: 38px; }
  .mascot {
    position: absolute;
    left: 700px;
    top: 0;
    width: 250px;
    height: 180px;
    background: radial-gradient(ellipse at 50% 45%, var(--mascot-green) 0%, var(--mascot-brown) 55%, rgba(154,90,42,0) 75%);
    opacity: 0.85;
  }
  .cta-button {
    position: absolute;
    left: 1012px;
    top: 80px;
    width: 150px;
    height: 40px;
    border-radius: 20px;
    background: var(--button-yellow);
    color: var(--button-text);
    font-size: 17px;
    font-weight: 800;
    display: flex;
    align-items: center;
    justify-content: center;
    text-decoration: none;
    letter-spacing: 0.3px;
  }
</style>
</head>
<body>
  <div class="banner">
    <svg class="banner__shapes" width="1200" height="180" viewBox="0 0 1200 180" aria-hidden="true">
      <defs>
        <linearGradient id="ctaFill" x1="0" y1="0" x2="1" y2="1">
          <stop offset="0" stop-color="var(--cta-red-light)"/>
          <stop offset="1" stop-color="var(--cta-red)"/>
        </linearGradient>
        <linearGradient id="panelFill" x1="0" y1="0" x2="0" y2="1">
          <stop offset="0" stop-color="var(--panel-green)"/>
          <stop offset="1" stop-color="var(--panel-green-deep)"/>
        </linearGradient>
      </defs>
      <polygon class="panel-message" fill="url(#panelFill)"
        points="88,8 638,8 696,70 696,110 638,172 88,172 29,110 29,70"/>
      <polygon class="panel-cta" fill="url(#ctaFill)"
        points="1012,14 1200,14 1200,168 1012,168 962,112 962,70"/>
    </svg>

    <div class="message">
      <p class="message__question">Need a Mortgage Broker?</p>
      <div class="message__rule"></div>
      <p class="message__line message__line--search">Search now on Australia’s</p>
      <p class="message__line message__line--directory">Largest Directory</p>
    </div>

    <div class="mascot" role="img" aria-label="Smiling cartoon turtle mascot holding a small house"></div>

    <a class="cta-button" href="#">CLICK HERE</a>
  </div>
</body>
</html>
```